Copperleaf Roofing Business Card

This is my current business card. But I’d like to make some changes. Somewhere on the card I’d like to list some of the services we offer. Maybe on the back? But I’d still like to keep the red. White and black modern look.

-residential & commercial roofing
-Roof Repairs & Maintenance
-Storm Damage & Insurance Claims specialist
-Christmas Lights and permanent Christmas lights
Fencing. Windows. Gutters. Siding. Sheetrock, painting.

```html
<!DOCTYPE html>
<html lang="en">
<head>
<meta charset="utf-8">
<title>Copperleaf Roofing Co. – Business Card</title>
<link rel="stylesheet" href="https://fonts.googleapis.com/css2?family=Michroma&family=Roboto+Condensed:wght@400;500&display=swap">
<style>
  :root {
    --red: #e01f26;
    --deep-red: #8c1015;
    --black: #111111;
    --white: #ffffff;
    --stage: #2e2e2e;
    --ink: #1a1a1a;
  }
  * { box-sizing: border-box; margin: 0; padding: 0; }
  html, body {
    width: 1200px;
    height: 694px;
    overflow: hidden;
    background: var(--stage);
  }
  .canvas {
    position: relative;
    width: 1200px;
    height: 694px;
  }
  .card {
    position: absolute;
    top: 187px;
    width: 540px;
    height: 320px;
    border-radius: 18px;
    overflow: hidden;
  }

  /* Back of card */
  .card-back { left: 30px; }
  .tartan-field {
    position: absolute;
    inset: 0;
    background: linear-gradient(135deg, var(--deep-red) 0%, var(--red) 45%, var(--deep-red) 75%, #3a0a0c 100%);
  }
  .back-brand {
    position: absolute;
    inset: 0;
    display: flex;
    flex-direction: column;
    align-items: center;
    justify-content: center;
    gap: 18px;
  }
  .brand-disc {
    width: 96px;
    height: 96px;
    border-radius: 50%;
    background: var(--black);
    border: 4px solid var(--white);
  }
  .back-brand .brand-name {
    font-family: "Michroma", sans-serif;
    color: var(--white);
    font-size: 25px;
    line-height: 1.3;
    text-align: center;
    letter-spacing: 1px;
  }

  /* Front of card */
  .card-front {
    left: 630px;
    background: var(--white);
  }
  .tartan-strip {
    position: absolute;
    left: 0;
    right: 0;
    bottom: 0;
    height: 26px;
    background: linear-gradient(90deg, var(--deep-red), var(--red) 40%, var(--black) 70%, var(--red));
  }
  .front-brand {
    position: absolute;
    left: 180px;
    top: 30px;
    display: flex;
    align-items: center;
    gap: 10px;
  }
  .front-brand .brand-disc-small {
    width: 44px;
    height: 44px;
    border-radius: 50%;
    background: var(--red);
  }
  .front-brand .brand-name {
    font-family: "Michroma", sans-serif;
    color: var(--red);
    font-size: 14px;
    line-height: 1.3;
    letter-spacing: 0.5px;
  }

  .contact {
    position: absolute;
    left: 28px;
    top: 160px;
  }
  .person-name {
    font-family: "Michroma", sans-serif;
    font-size: 22px;
    letter-spacing: 1px;
    color: var(--black);
  }
  .person-name .first { color: var(--red); }
  .person-role {
    font-family: "Roboto Condensed", sans-serif;
    font-size: 15px;
    color: var(--ink);
    margin: 2px 0 10px;
  }
  .contact-list { list-style: none; }
  .contact-list li {
    display: flex;
    align-items: center;
    gap: 8px;
    font-family: "Roboto Condensed", sans-serif;
    font-size: 13.5px;
    color: var(--ink);
    margin-bottom: 4px;
  }
  .contact-list svg { width: 14px; height: 14px; flex: none; }

  .services {
    position: absolute;
    left: 290px;
    top: 110px;
    width: 240px;
    list-style: none;
    font-family: "Roboto Condensed", sans-serif;
    font-size: 12.5px;
    line-height: 1.55;
    color: var(--ink);
  }
  .services li::before {
    content: "•";
    color: var(--red);
    margin-right: 5px;
  }
  .services .dot { color: var(--red); margin: 0 3px; }
</style>
</head>
<body>
<main class="canvas">

  <section class="card card-back" aria-label="Card back">
    <div class="tartan-field" role="img" aria-label="Red, black and white tartan plaid pattern"></div>
    <div class="back-brand">
      <div class="brand-disc"></div>
      <div class="brand-name">COPPERLEAF<br>ROOFING CO.</div>
    </div>
  </section>

  <section class="card card-front" aria-label="Card front">
    <div class="front-brand">
      <div class="brand-disc-small"></div>
      <div class="brand-name">COPPERLEAF<br>ROOFING CO.</div>
    </div>

    <div class="contact">
      <h1 class="person-name"><span class="first">DANA</span> KERR</h1>
      <p class="person-role">Owner</p>
      <ul class="contact-list">
        <li>
          <svg viewBox="0 0 16 16" aria-hidden="true"><path fill="#e01f26" d="M3.5 1.5l2.5 3-1.5 1.5c.8 2 2.5 3.7 4.5 4.5l1.5-1.5 3 2.5-1.5 2.5C7 14 2 9 1 3z"/></svg>
          555-014-2290
        </li>
        <li>
          <svg viewBox="0 0 16 16" aria-hidden="true"><rect x="1" y="3" width="14" height="10" fill="#e01f26"/><path d="M1 3l7 6 7-6" fill="none" stroke="#fff" stroke-width="1.3"/></svg>
          dana@copperleafroofing.co
        </li>
        <li>
          <svg viewBox="0 0 16 16" aria-hidden="true"><circle cx="8" cy="8" r="7" fill="#e01f26"/><ellipse cx="8" cy="8" rx="3" ry="7" fill="none" stroke="#fff" stroke-width="1"/><path d="M1 8h14" stroke="#fff" stroke-width="1"/></svg>
          www.copperleafroofing.co
        </li>
      </ul>
    </div>

    <ul class="services">
      <li>Residential &amp; commercial roofing</li>
      <li>Roof Repairs &amp; Maintenance</li>
      <li>Storm Damage &amp; Insurance Claims specialist</li>
      <li>Christmas Lights and permanent Christmas lights</li>
      <li>Fencing <span class="dot">•</span> Windows <span class="dot">•</span> Gutters <span class="dot">•</span> Siding</li>
      <li>Sheetrock <span class="dot">•</span> Painting</li>
    </ul>

    <div class="tartan-strip" role="img" aria-label="Red, black and white tartan plaid band"></div>
  </section>

</main>
</body>
</html>
```